tinyTally Resource Book - 10 maths tasks to do outside

I need a 22 (11 pages back to back) page A6 sized book produced to standard for submission to professional printer. Needs to be as .pdf file showing guide lines and allowances for colour bleed. I have text already written and submitted as attachment in a Word file with margins set to A6 size. The theme of the materials is "Nature Play" so using lots of pictures from nature (Australia preferably) and showing lots of patterns in nature (rocks, leaves, flower petals etc). Some of the tasks refer to specific activities, such as "shadows" and "floating" so would be great to illustrate appropriately. The big emphasis is on learning outside the classroom, getting kids to engage actively with nature. I would like to see the pages as full colour - so not white background. The book itself will be spiral bound along the top edge so a margin of at least 1cm will be required at the top of each page (or the bottom of even numbered pages). Book will be printed on plastic laminated matte paper for outdoor use. Font size needs to be big enough to read. Fonts sizes, alignments and page numbers are all different at the moment and need to be standardised. One photo is included in a page as a sample if you can use it, otherwise disregard. Logo for Wattlebrook Numeracy Guild is also included to have as part of the acknowledgements at the back of the book.

Target Market(s)

Book is for early childhood and preschool teachers.

Industry/Entity Type

Education

Font styles to use
Sans Serif

Requirements
Must have
• Colour and appeal.
Nice to have
• Use of natural colours instead of bright catchy colours but that is your call.
Should not have
• American spelling

```html
<!DOCTYPE html>
<html lang="en-AU">
<head>
<meta charset="utf-8">
<title>Make a Star – tinyTally Resource Book</title>
<link rel="stylesheet" href="https://fonts.googleapis.com/css2?family=Fredoka:wght@600;700&family=Didact+Gothic&display=swap">
<style>
  :root {
    --paper: #ffffff;
    --page-light: #dcd3c8;
    --page-mid: #cfc5b9;
    --page-dark: #bfb3a6;
    --heading-blue: #2c3a94;
    --heading-edge: #ffffff;
    --bullet-red: #d8262c;
    --body-ink: #3b3835;
    --crop-ink: #555555;
    --photo-top: #7d6c58;
    --photo-base: #5a4a3c;
  }
  * { margin: 0; padding: 0; box-sizing: border-box; }
  html, body { width: 892px; height: 1200px; overflow: hidden; background: var(--paper); }
  .sheet { position: relative; width: 892px; height: 1200px; }
  .crop-marks { position: absolute; inset: 0; }
  .page-bleed {
    position: absolute; left: 53px; top: 53px; width: 786px; height: 1093px;
    background: linear-gradient(160deg, var(--page-light), var(--page-mid) 55%, var(--page-dark));
  }
  .content { position: absolute; inset: 0; font-family: "Didact Gothic", sans-serif; color: var(--body-ink); }
  .heading {
    position: absolute; left: 125px; font-family: "Fredoka", sans-serif; font-weight: 700;
    color: var(--heading-blue); -webkit-text-stroke: 3px var(--heading-edge); paint-order: stroke fill;
    line-height: 1; white-space: nowrap;
  }
  .heading--title { top: 140px; font-size: 57px; }
  .heading--section { font-size: 48px; }
  .heading--prompts { top: 449px; }
  .heading--variations { top: 609px; }
  .heading--ideas { top: 879px; }
  .bullet-list {
    position: absolute; left: 186px; list-style: none; font-size: 32px; line-height: 36.4px;
    white-space: nowrap;
  }
  .bullet-list li { position: relative; padding-left: 32px; }
  .bullet-list li::before {
    content: ""; position: absolute; left: 3px; top: 11px; width: 15px; height: 15px;
    background: var(--bullet-red); transform: rotate(45deg);
  }
  .task-steps { top: 192px; }
  .prompts { top: 496px; }
  .variations { top: 656px; }
  .big-ideas { top: 926px; }
  .activity-photo {
    position: absolute; left: 510px; top: 730px; width: 258px; height: 360px;
    background: linear-gradient(180deg, var(--photo-top) 0%, var(--photo-base) 100%);
    box-shadow: 2px 2px 6px rgba(0,0,0,0.35);
  }
  .page-number { position: absolute; left: 697px; top: 1022px; width: 70px; height: 66px; }
  .page-number svg { position: absolute; inset: 0; }
  .page-number span {
    position: absolute; left: 0; right: 0; top: 18px; text-align: center;
    font-family: "Didact Gothic", sans-serif; color: #fff; font-size: 32px; line-height: 40px;
  }
</style>
</head>
<body>
<div class="sheet">
  <div class="page-bleed" role="img" aria-label="Faded photograph of river stones laid out on timber decking"></div>

  <svg class="crop-marks" width="892" height="1200" viewBox="0 0 892 1200" aria-hidden="true">
    <g stroke="var(--crop-ink)" stroke-width="1">
      <line x1="53" y1="0" x2="53" y2="48"/><line x1="74" y1="0" x2="74" y2="48"/>
      <line x1="0" y1="53" x2="48" y2="53"/><line x1="0" y1="74" x2="48" y2="74"/>
      <line x1="839" y1="0" x2="839" y2="48"/><line x1="818" y1="0" x2="818" y2="48"/>
      <line x1="844" y1="53" x2="892" y2="53"/><line x1="844" y1="74" x2="892" y2="74"/>
      <line x1="53" y1="1152" x2="53" y2="1200"/><line x1="74" y1="1152" x2="74" y2="1200"/>
      <line x1="0" y1="1146" x2="48" y2="1146"/><line x1="0" y1="1126" x2="48" y2="1126"/>
      <line x1="839" y1="1152" x2="839" y2="1200"/><line x1="818" y1="1152" x2="818" y2="1200"/>
      <line x1="844" y1="1146" x2="892" y2="1146"/><line x1="844" y1="1126" x2="892" y2="1126"/>
    </g>
  </svg>

  <div class="content">
    <h1 class="heading heading--title">7. Make a Star</h1>
    <ul class="bullet-list task-steps">
      <li>&nbsp;Put down a number of objects in a cir-<br>cle or bunch</li>
      <li>&nbsp;Partner puts down a corresponding ob-<br>ject on the outside of the circle, one for<br>each original object</li>
      <li>Keep adding objects to each arm of the<br>star as it grows</li>
    </ul>

    <h2 class="heading heading--section heading--prompts">Prompting questions</h2>
    <ul class="bullet-list prompts">
      <li>How big can you make the star?</li>
      <li>Does each arm of the star need to have<br>the same number of objects?</li>
    </ul>

    <h2 class="heading heading--section heading--variations">Variations</h2>
    <ul class="bullet-list variations">
      <li>Start with different numbers of objects –<br>3 (triangle), 4 (square) etc and compare<br>the resulting stars</li>
      <li>Use combinations<br>of different materials<br>to grow star</li>
    </ul>

    <h2 class="heading heading--section heading--ideas">Big Ideas</h2>
    <ul class="bullet-list big-ideas">
      <li>Repeated addition</li>
      <li>Symmetry</li>
      <li>Growing patterns</li>
      <li>Decreasing patterns</li>
    </ul>

    <div class="activity-photo" role="img" aria-label="Photograph of a child in a sun hat arranging stones into a star shape on decking"></div>

    <div class="page-number">
      <svg width="70" height="66" viewBox="0 0 70 66" aria-hidden="true">
        <polygon points="35,0 70,25 57,66 13,66 0,25" fill="var(--heading-blue)"/>
      </svg>
      <span>15</span>
    </div>
  </div>
</div>
</body>
</html>
```